Business Card Design Project

Business card based on attached logo

Todd Merrick
Todd@lorvantest.com
877-514-9073 ext. 318
Www.LorvanTest.com

Industry/Entity Type

Business

```html
<!DOCTYPE html>
<html lang="en">
<head>
<meta charset="utf-8">
<title>LorvanTest Business Cards</title>
<link rel="stylesheet" href="https://fonts.googleapis.com/css2?family=Archivo:wght@400;500;700;800&display=swap">
<style>
  :root {
    --ink: #231f20;
    --red: #ec1c24;
    --black: #231f20;
    --white: #ffffff;
    --light-1: #f6f6f6;
    --light-2: #e4e4e5;
    --stage: #ece9e4;
  }
  * { box-sizing: border-box; margin: 0; padding: 0; }
  html, body {
    width: 1200px;
    height: 715px;
    overflow: hidden;
    background: var(--stage);
    font-family: "Archivo", Arial, sans-serif;
  }
  .sheet { position: relative; width: 1200px; height: 715px; }

  .card {
    position: absolute;
    width: 508px;
    height: 290px;
    border-radius: 82px 0 82px 0;
    border: 1px solid #3a3a3a;
    overflow: hidden;
  }
  .card--front  { left: 50px;  top: 36px; }
  .card--light  { left: 622px; top: 36px; }
  .card--red    { left: 46px;  top: 378px; }
  .card--black  { left: 628px; top: 381px; }

  .card--front, .card--light {
    background: radial-gradient(ellipse at 55% 35%, var(--light-1) 0%, var(--light-2) 100%);
    color: var(--ink);
  }
  .card--red   { background: var(--red);   color: var(--white); border-color: var(--red); }
  .card--black { background: var(--black); color: var(--white); }

  .wordmark {
    position: absolute;
    left: 0; right: 0;
    display: flex;
    justify-content: center;
    align-items: flex-start;
    gap: 8px;
  }
  .wordmark__name {
    font-weight: 800;
    letter-spacing: -1px;
    line-height: 1;
  }
  .wordmark__mark {
    width: 16px; height: 16px;
    background: var(--red);
    margin-top: 2px;
  }
  .card--red .wordmark__mark,
  .card--black .wordmark__mark { background: var(--white); }

  .card--front .wordmark { top: 74px; }
  .card--front .wordmark__name { font-size: 64px; }
  .card--light .wordmark,
  .card--red .wordmark,
  .card--black .wordmark { top: 92px; }
  .card--light .wordmark__name,
  .card--red .wordmark__name,
  .card--black .wordmark__name { font-size: 76px; }
  .card--light .wordmark__mark,
  .card--red .wordmark__mark,
  .card--black .wordmark__mark { width: 19px; height: 19px; }

  .holder {
    position: absolute;
    top: 203px; left: 0; right: 0;
    text-align: center;
    color: var(--red);
    font-weight: 700;
    font-size: 16px;
    letter-spacing: 1.6px;
  }
  .contact {
    position: absolute;
    top: 236px; left: 0; right: 0;
    display: flex;
    justify-content: center;
    gap: 14px;
    font-size: 12.5px;
    color: var(--ink);
  }
  .contact__item { display: flex; align-items: center; gap: 5px; }
  .contact__item svg { width: 11px; height: 11px; fill: var(--ink); }

  .web {
    position: absolute;
    left: 0; right: 0;
    display: flex;
    justify-content: center;
    align-items: center;
    gap: 6px;
    font-size: 13.5px;
    letter-spacing: 2.2px;
  }
  .web svg { width: 11px; height: 11px; }
  .card--front .web { top: 264px; font-size: 12.5px; }
  .card--light .web { top: 263px; }
  .card--red .web,
  .card--black .web { top: 264px; }
</style>
</head>
<body>
<main class="sheet">

  <section class="card card--front">
    <div class="wordmark">
      <span class="wordmark__name">LorvanTest</span>
      <span class="wordmark__mark"></span>
    </div>
    <p class="holder">Todd Merrick</p>
    <div class="contact">
      <span class="contact__item">
        <svg viewBox="0 0 24 24" aria-hidden="true"><path d="M6.6 10.8a15 15 0 0 0 6.6 6.6l2.2-2.2c.3-.3.7-.4 1-.2 1.1.4 2.3.6 3.6.6.6 0 1 .4 1 1V20c0 .6-.4 1-1 1A17 17 0 0 1 3 4c0-.6.4-1 1-1h3.5c.6 0 1 .4 1 1 0 1.3.2 2.5.6 3.6.1.3 0 .7-.2 1z"/></svg>
        877-514-9073 ext. 318
      </span>
      <span class="contact__item">
        <svg viewBox="0 0 24 24" aria-hidden="true"><path d="M2 6h20v13H2zM3.5 7.5 12 13l8.5-5.5z" fill-rule="evenodd"/></svg>
        Todd@lorvantest.com
      </span>
    </div>
    <p class="web">
      <svg viewBox="0 0 24 24" aria-hidden="true"><circle cx="12" cy="12" r="10" fill="none" stroke="#231f20" stroke-width="2.4"/><path d="M2 12h20M12 2c3 3 3 17 0 20M12 2c-3 3-3 17 0 20" fill="none" stroke="#231f20" stroke-width="2"/></svg>
      www.LorvanTest.com
    </p>
  </section>

  <section class="card card--light">
    <div class="wordmark">
      <span class="wordmark__name">LorvanTest</span>
      <span class="wordmark__mark"></span>
    </div>
    <p class="web">www.LorvanTest.com</p>
  </section>

  <section class="card card--red">
    <div class="wordmark">
      <span class="wordmark__name">LorvanTest</span>
      <span class="wordmark__mark"></span>
    </div>
    <p class="web">www.LorvanTest.com</p>
  </section>

  <section class="card card--black">
    <div class="wordmark">
      <span class="wordmark__name">LorvanTest</span>
      <span class="wordmark__mark"></span>
    </div>
    <p class="web">www.LorvanTest.com</p>
  </section>

</main>
</body>
</html>
```